Redesign of business card for Cedar Ridge Mechanical

We are looking for a new design for our business cards for Cedar Ridge Mechanical. We are a plumbing & HVAC construction company, operating on the West Coast of Canada and USA. Logo attached.
Industry/Entity Type
Construction - Plumbing & HVAC
Contact Information for Business Card
Name, address, phone numbers, email, website address
Look and feel
Each slider illustrates characteristics of the customer's brand and the style your logo design should communicate.

```html
<!DOCTYPE html>
<html lang="en">
<head>
<meta charset="utf-8">
<title>Cedar Ridge Mechanical – Business Card</title>
<link href="https://fonts.googleapis.com/css2?family=Exo+2:ital,wght@1,900&family=Oswald:wght@500&family=Roboto:wght@400&display=swap" rel="stylesheet">
<style>
  :root {
    --navy: #24426f;
    --gold: #d4bf8a;
    --white: #ffffff;
    --backdrop: #e9e9e9;
  }
  * { box-sizing: border-box; margin: 0; padding: 0; }
  html, body { width: 1200px; height: 1200px; overflow: hidden; }
  body { background: var(--backdrop); position: relative; font-family: "Roboto", Arial, sans-serif; }

  .card {
    position: absolute;
    left: 233px;
    width: 730px;
    height: 416px;
    border-radius: 36px;
    overflow: hidden;
  }
  .card--front { top: 150px; background: var(--white); }
  .card--back { top: 651px; background: var(--navy); }

  .brand {
    position: absolute;
    display: flex;
    align-items: center;
    gap: 14px;
    font-family: "Oswald", "Arial Narrow", sans-serif;
    font-weight: 500;
    text-transform: uppercase;
    line-height: 1.05;
    letter-spacing: 1px;
  }
  .brand__mark { flex: none; }
  .brand--front { left: 68px; top: 168px; color: var(--navy); font-size: 34px; }
  .brand--front .brand__mark { width: 26px; height: 26px; background: var(--navy); }
  .brand--back { left: 0; right: 0; top: 160px; justify-content: center; color: var(--white); font-size: 46px; }
  .brand--back .brand__mark { width: 34px; height: 34px; background: var(--white); }

  .person { position: absolute; left: 416px; top: 66px; color: var(--navy); }
  .person__name {
    font-family: "Exo 2", Arial, sans-serif;
    font-style: italic;
    font-weight: 900;
    font-size: 31px;
    letter-spacing: -0.5px;
    line-height: 1;
  }
  .person__role { font-size: 16px; margin-top: 6px; }

  .contact-rail {
    position: absolute;
    left: 417px;
    top: 159px;
    width: 29px;
    height: 112px;
    background: var(--gold);
    border-radius: 5px;
  }
  .contact-rail svg { position: absolute; left: 8px; width: 13px; height: 13px; }

  .contact-list {
    position: absolute;
    left: 459px;
    top: 156px;
    list-style: none;
    color: var(--navy);
    font-size: 17.5px;
    line-height: 28.3px;
  }

  .address {
    position: absolute;
    left: 416px;
    top: 301px;
    color: var(--navy);
    font-size: 17.5px;
    line-height: 22.5px;
  }
</style>
</head>
<body>

<section class="card card--front">
  <div class="brand brand--front">
    <span class="brand__mark"></span>
    <span class="brand__name">Cedar Ridge<br>Mechanical</span>
  </div>

  <div class="person">
    <h1 class="person__name">MY NAME</h1>
    <p class="person__role">Founder &amp; Director</p>
  </div>

  <div class="contact-rail" aria-hidden="true">
    <svg style="top:8px" viewBox="0 0 16 16"><path fill="#fff" d="M3 1.5l2.5-.5 1.5 3.5-1.6 1.2a8 8 0 0 0 4.9 4.9l1.2-1.6 3.5 1.5-.5 2.5c-.2.8-1 1.3-1.8 1.2C6.9 13.7 2.3 9.1 1.8 3.3 1.7 2.5 2.2 1.7 3 1.5z"/></svg>
    <svg style="top:36px" viewBox="0 0 16 16"><rect x="4" y="1" width="8" height="14" rx="1.5" fill="none" stroke="#fff" stroke-width="1.5"/></svg>
    <svg style="top:64px" viewBox="0 0 16 16"><rect x="1" y="3" width="14" height="10" rx="1" fill="#fff"/><path d="M1.5 3.5L8 9l6.5-5.5" fill="none" stroke="#d4bf8a" stroke-width="1.2"/></svg>
    <svg style="top:92px" viewBox="0 0 16 16"><g fill="none" stroke="#fff" stroke-width="1.3"><circle cx="8" cy="8" r="6.5"/><ellipse cx="8" cy="8" rx="3" ry="6.5"/><path d="M1.5 8h13M2.5 4.8h11M2.5 11.2h11"/></g></svg>
  </div>

  <ul class="contact-list">
    <li>845 845 8456</li>
    <li>458 458 4569</li>
    <li>info@websitename.com</li>
    <li>www.websitename.com</li>
  </ul>

  <p class="address">P.O. Box, Street Name,<br>Countryname , ZIPCODE 0000</p>
</section>

<section class="card card--back">
  <div class="brand brand--back">
    <span class="brand__mark"></span>
    <span class="brand__name">Cedar Ridge Mechanical</span>
  </div>
</section>

</body>
</html>
```